Business Card for a New Zealand IT Startup

I need a business card for VELTA Holdings. We are a young startup based in New Zealand working in internet marketing and web development. The design should have some element connected to New Zealand, such as wave, koru or silver fern, just don't use a kiwi bird.

```html
<!DOCTYPE html>
<html lang="en">
<head>
<meta charset="utf-8">
<title>VELTA Holdings – Business Card</title>
<link rel="stylesheet" href="https://fonts.googleapis.com/css2?family=Open+Sans:wght@400;600;700&display=swap">
<style>
  :root {
    --bg: #2e2f31;
    --orange: #ee5a22;
    --blue: #0b66b0;
    --white: #ffffff;
    --ink: #3a3a3a;
  }
  html, body {
    margin: 0;
    padding: 0;
    width: 1200px;
    height: 1000px;
    overflow: hidden;
    background: var(--bg);
    font-family: "Open Sans", Arial, sans-serif;
  }
  .canvas {
    position: relative;
    width: 1200px;
    height: 1000px;
  }
  .card {
    position: absolute;
    left: 250px;
    width: 700px;
    height: 400px;
    overflow: hidden;
    box-shadow: 0 10px 30px rgba(0,0,0,0.45);
  }
  .card-back {
    top: 70px;
    background: var(--orange);
    display: flex;
    align-items: center;
    justify-content: center;
  }
  .back-brand {
    color: var(--white);
    font-weight: 700;
    font-size: 44px;
    letter-spacing: 2px;
  }
  .card-front {
    top: 530px;
    background: var(--white);
  }
  .front-shapes {
    position: absolute;
    inset: 0;
  }
  .brand {
    position: absolute;
    left: 40px;
    top: 36px;
    display: flex;
    align-items: center;
    gap: 12px;
    color: var(--blue);
    font-weight: 700;
    font-size: 34px;
    letter-spacing: 1px;
  }
  .brand-dot {
    width: 30px;
    height: 30px;
    border-radius: 50%;
    background: var(--blue);
  }
  .address {
    position: absolute;
    left: 40px;
    top: 150px;
    margin: 0;
    font-style: normal;
    font-size: 17px;
    line-height: 22px;
    color: var(--ink);
  }
  .contacts {
    position: absolute;
    left: 40px;
    top: 200px;
    margin: 0;
    padding: 0;
    list-style: none;
    font-size: 17px;
    line-height: 24px;
    color: var(--ink);
  }
  .contacts li {
    display: flex;
    align-items: center;
    gap: 8px;
  }
  .contacts svg {
    width: 16px;
    height: 16px;
    fill: var(--blue);
    flex: none;
  }
  .contacts .no-icon {
    padding-left: 24px;
  }
  .person {
    position: absolute;
    right: 180px;
    top: 190px;
    text-align: right;
  }
  .person-name {
    margin: 0;
    color: var(--blue);
    font-weight: 700;
    font-size: 22px;
    letter-spacing: 0.5px;
  }
  .person-role {
    margin: 0;
    color: var(--orange);
    font-weight: 600;
    font-size: 17px;
    letter-spacing: 0.5px;
  }
</style>
</head>
<body>
<main class="canvas">
  <section class="card card-back" aria-label="Card back">
    <span class="back-brand">VELTA Holdings</span>
  </section>

  <section class="card card-front" aria-label="Card front">
    <svg class="front-shapes" viewBox="0 0 700 400" preserveAspectRatio="none" aria-hidden="true">
      <rect width="700" height="400" fill="var(--blue)"/>
      <path d="M0,0 H540 C690,30 720,230 620,310 C540,370 360,385 300,400 H0 Z" fill="var(--white)"/>
      <path d="M300,400 C420,370 590,350 640,230 C650,310 600,370 500,400 Z" fill="var(--orange)"/>
    </svg>

    <div class="brand">
      <span class="brand-dot"></span>
      <span>VELTA Holdings</span>
    </div>

    <address class="address">27 Harbour View Road<br>Wellington 6011</address>

    <ul class="contacts" style="top:200px">
      <li>
        <svg viewBox="0 0 16 16"><path d="M3 1h3l1 4-2 1c1 2 3 4 5 5l1-2 4 1v3c0 1-1 2-2 2C7 15 1 9 1 3c0-1 1-2 2-2z"/></svg>
        021 455 8190
      </li>
      <li>
        <svg viewBox="0 0 16 16"><path d="M4 0h8a1 1 0 0 1 1 1v14a1 1 0 0 1-1 1H4a1 1 0 0 1-1-1V1a1 1 0 0 1 1-1zm1 2v10h6V2z"/></svg>
        022 613 4478
      </li>
      <li>
        <svg viewBox="0 0 16 16"><path d="M4 1h8v4H4zM1 6h14v7h-3v2H4v-2H1zm4 5v3h6v-3z"/></svg>
        04 382 9605
      </li>
      <li>
        <svg viewBox="0 0 16 16"><path d="M1 3h14v10H1zm1 1v1l6 4 6-4V4z"/></svg>
        mara@veltaholdings.com
      </li>
      <li>
        <svg viewBox="0 0 16 16"><circle cx="8" cy="8" r="7"/></svg>
        www.veltaholdings.com
      </li>
      <li class="no-icon">www.veltaholdings.com</li>
    </ul>

    <div class="person">
      <p class="person-name">MARA TANE</p>
      <p class="person-role">PRESIDENT</p>
    </div>
  </section>
</main>
</body>
</html>
```